Irrigation Business needs their business cards modernised and revamped

I would like to keep my current logo, colours and revamp the format of the card.

I would like the card to be clean yet important.

Im not sure if you include texture but i would like the named logo to be indented into the card etc.

show me something alive and free something thats clinical to the point yet has a feel of achievement. i would like people to go nice card.

Target Market(s)

high end clients, corporate, sports field manger, the guys that make the decisions

Industry/Entity Type

Business

Contact Information for Business Card

nformation to be included

Dean Harlow (Director)
0487305526
dean@kolvat.biz
www.kestonfieldworks.com

instagram logo
google logo
facebook logo

Colors

Designer to choose colors to be used in the design.

Requirements
Nice to have
• indentations a really nice feel to the card good texture

```html
<!DOCTYPE html>
<html lang="en">
<head>
<meta charset="utf-8">
<title>Keston Fieldworks – Business Card</title>
<link href="https://fonts.googleapis.com/css2?family=Montserrat:wght@700;800&family=Open+Sans:wght@400;600&display=swap" rel="stylesheet">
<style>
  :root {
    --brand-blue: #2f6cb3;
    --sky-blue: #2fa8d8;
    --card-white: #ffffff;
    --ink-grey: #6b6b6b;
    --backdrop: #e9ecef;
  }
  html, body {
    margin: 0;
    padding: 0;
    width: 1200px;
    height: 900px;
    overflow: hidden;
    background: var(--backdrop);
  }
  .canvas {
    position: relative;
    width: 1200px;
    height: 900px;
  }
  .card {
    position: absolute;
    width: 700px;
    height: 427px;
    border-radius: 22px;
    box-shadow: 0 10px 28px rgba(0,0,0,0.18);
    overflow: hidden;
  }
  .card-back {
    left: 450px;
    top: 40px;
    background: var(--brand-blue);
    color: var(--card-white);
    display: flex;
    flex-direction: column;
    align-items: center;
    justify-content: center;
  }
  .card-front {
    left: 50px;
    top: 430px;
    background: var(--card-white);
  }
  .back-mark {
    width: 86px;
    height: 86px;
    border-radius: 50%;
    border: 5px solid var(--card-white);
    box-sizing: border-box;
    margin-bottom: 18px;
  }
  .back-name {
    font-family: "Montserrat", sans-serif;
    font-weight: 800;
    font-size: 34px;
    letter-spacing: 0.5px;
    text-transform: uppercase;
    margin: 0;
  }
  .back-url {
    font-family: "Open Sans", sans-serif;
    font-size: 17px;
    margin-top: 40px;
    letter-spacing: 0.3px;
  }
  .front-art { display: block; }
  .logo-name { font-family: "Montserrat", sans-serif; font-weight: 800; font-size: 30px; fill: var(--brand-blue); text-transform: uppercase; }
  .person-name { font-family: "Montserrat", sans-serif; font-weight: 700; font-size: 25px; fill: var(--brand-blue); }
  .person-role { font-family: "Open Sans", sans-serif; font-size: 16px; fill: var(--ink-grey); }
  .contact-text { font-family: "Open Sans", sans-serif; font-size: 17px; fill: var(--card-white); }
</style>
</head>
<body>
<main class="canvas">

  <section class="card card-back" role="img" aria-label="Card back: blue field with a faint water-drop pattern">
    <div class="back-mark"></div>
    <h1 class="back-name">Keston Fieldworks</h1>
    <div class="back-url">www.kestonfieldworks.com</div>
  </section>

  <section class="card card-front">
    <svg class="front-art" width="700" height="427" viewBox="0 0 700 427" xmlns="http://www.w3.org/2000/svg">
      <text class="logo-name" x="40" y="70">Keston Fieldworks</text>
      <text class="person-name" x="40" y="150">DEAN HARLOW</text>
      <text class="person-role" x="40" y="174">Director</text>

      <g class="contact-band">
        <rect x="0" y="205" width="700" height="222" fill="var(--brand-blue)"/>
        <rect x="0" y="212" width="700" height="5" fill="var(--card-white)"/>
        <rect x="0" y="250" width="700" height="5" fill="var(--card-white)"/>
        <rect x="0" y="288" width="700" height="5" fill="var(--card-white)"/>
        <rect x="0" y="326" width="700" height="5" fill="var(--card-white)"/>
      </g>

      <g class="feature-emblem" role="img" aria-label="Large company emblem area">
        <circle cx="560" cy="300" r="160" fill="var(--sky-blue)"/>
      </g>

      <g class="contact-icons" fill="none" stroke="var(--card-white)" stroke-width="1.8" stroke-linecap="round">
        <path class="icon-phone" d="M44 230 q0 10 10 12 l3 -3 l-3 -3 l-2 2 q-4 -2 -5 -6 l2 -2 l-3 -3 z"/>
        <rect class="icon-mail" x="43" y="262" width="16" height="11" rx="1"/>
        <path d="M43 263 l8 6 l8 -6"/>
        <circle class="icon-globe" cx="51" cy="309" r="8"/>
        <path d="M43 309 h16 M51 301 q-5 8 0 16 M51 301 q5 8 0 16"/>
      </g>
      <text class="contact-text" x="72" y="242">0487305526</text>
      <text class="contact-text" x="72" y="280">dean@kolvat.biz</text>
      <text class="contact-text" x="72" y="318">www.kestonfieldworks.com</text>

      <g class="social-dots" fill="var(--card-white)">
        <circle cx="52" cy="360" r="10"/>
        <circle cx="78" cy="360" r="10"/>
        <circle cx="104" cy="360" r="10"/>
      </g>
    </svg>
  </section>

</main>
</body>
</html>
```